Wealth Education Business Needs Sharp Business Card Design

We need a business card design for a recently launched investor education business called Harbor Crest.

The final design should promote security, empowerment, self improvement and financial gain. The card will ideally promote the stature of the business.

For more information and colours please visit harborcrest.com.au

Target Market(s)

Corporate executives and high net worth individuals

Industry/Entity Type

Education

Contact Information for Business Card

```html
<!DOCTYPE html>
<html lang="en">
<head>
<meta charset="utf-8">
<title>Harbor Crest – Business Card</title>
<link rel="stylesheet" href="https://fonts.googleapis.com/css2?family=Lato:wght@400;700&display=swap">
<style>
  :root {
    --page-bg: #e9e8e6;
    --card-top: #f4f5f6;
    --card-bottom: #e3e6e9;
    --ink: #1f2326;
    --brand-ink: #2b2f33;
    --teal: #1f7b78;
    --icon: #2f7f8c;
    --blue: #4d6a9e;
    --teal-band: #1b8a84;
    --green: #5ba24b;
  }
  * { margin: 0; padding: 0; box-sizing: border-box; }
  html, body {
    width: 1200px; height: 970px; overflow: hidden;
    background: var(--page-bg);
    font-family: "Lato", Arial, sans-serif;
  }
  .card {
    position: absolute; left: 80px; top: 192px;
    width: 1040px; height: 585px;
    border-radius: 22px; overflow: hidden;
    background: linear-gradient(180deg, var(--card-top), var(--card-bottom));
    box-shadow: 0 14px 40px rgba(0,0,0,0.18);
  }
  .card-artwork {
    position: absolute; left: 0; right: 0; bottom: 0; height: 160px;
    background:
      linear-gradient(180deg, rgba(77,106,158,0) 0%, rgba(77,106,158,0.55) 30%, rgba(27,138,132,0.85) 60%, var(--green) 100%);
  }
  .brand {
    position: absolute; left: 115px; top: 82px;
    display: flex; align-items: center; gap: 18px;
  }
  .brand-dot { width: 40px; height: 40px; border-radius: 50%; background: var(--icon); }
  .brand-name {
    font-weight: 700; font-size: 42px; letter-spacing: 5px;
    color: var(--brand-ink); text-transform: uppercase;
  }
  .person { position: absolute; right: 45px; top: 40px; text-align: right; }
  .person-name { font-size: 36px; font-weight: 700; color: var(--teal); line-height: 1.1; }
  .person-role { font-size: 26px; font-weight: 700; color: var(--ink); margin-top: 6px; }
  .contacts {
    position: absolute; right: 45px; top: 160px;
    list-style: none; text-align: right;
    font-size: 26px; color: var(--ink); line-height: 35px;
  }
  .contacts li { display: flex; justify-content: flex-end; align-items: center; gap: 12px; }
  .contacts .gap { margin-top: 24px; }
  .contacts .no-icon { padding-right: 38px; }
  .icon { width: 26px; height: 26px; fill: var(--icon); flex: none; }
</style>
</head>
<body>
  <div class="card">
    <div class="card-artwork" role="img" aria-label="Decorative sweeping blue, teal and green wave artwork"></div>

    <div class="brand">
      <span class="brand-dot"></span>
      <span class="brand-name">Harbor Crest</span>
    </div>

    <div class="person">
      <p class="person-name">Marcus Hale</p>
      <p class="person-role">Director</p>
    </div>

    <ul class="contacts">
      <li>1300 555 018
        <svg class="icon" viewBox="0 0 24 24"><path d="M3 9c0-3 4-5 9-5s9 2 9 5v2h-5V9c-1-1-7-1-8 0v2H3z M6 13h12l2 7H4z"/></svg>
      </li>
      <li>+613 5550 1234
        <svg class="icon" viewBox="0 0 24 24"><path d="M7 2h10a2 2 0 0 1 2 2v16a2 2 0 0 1-2 2H7a2 2 0 0 1-2-2V4a2 2 0 0 1 2-2zm0 3v13h10V5z"/></svg>
      </li>
      <li>support@harborcrest.com.au
        <svg class="icon" viewBox="0 0 24 24"><path d="M2 5h20v14H2z M3 6l9 7 9-7" stroke="#fff" stroke-width="1.5"/></svg>
      </li>
      <li>www.harborcrest.com.au
        <svg class="icon" viewBox="0 0 24 24"><circle cx="12" cy="12" r="10"/><path d="M2 12h20M12 2c-4 5-4 15 0 20M12 2c4 5 4 15 0 20" stroke="#fff" stroke-width="1.4" fill="none"/></svg>
      </li>
      <li class="gap">Level 3, 42 Quayside Lane
        <svg class="icon" viewBox="0 0 24 24"><path d="M12 3l10 9h-3v9h-5v-6h-4v6H5v-9H2z"/></svg>
      </li>
      <li class="no-icon">Melbourne VIC 3000</li>
    </ul>
  </div>
</body>
</html>
```